Need webdesign for service company that provides Car hiring service and transit service

We need a web design for a company that provides airport transit services and transport services including Limo, Corporate cars, Disability transit, Family transit service. We need is a simple and professional design.

Below is site which we like and also offer the same service http://www.ridelarkway.com.au/
Updates

Project Deadline Extended
Reason: Waiting for the Feedback from multiple stakeholders. Need the time to select and approve the design

Target Market(s)

Tourism, Travel

Industry/Entity Type

Airport

Number of Pages Required

3 page

Font styles to use
Decorative
Script

Requirements
Must have
• Simple and Professional, Site we like http://www.ridelarkway.com.au/ and also need to mobile friendly
Should not have
• Shouldn't have too many images

```html
<!DOCTYPE html>
<html lang="en">
<head>
<meta charset="utf-8">
<title>RouteWell – Private &amp; Business Transport</title>
<link rel="stylesheet" href="https://fonts.googleapis.com/css2?family=Montserrat:wght@400;500&family=Open+Sans:wght@400&display=swap">
<style>
  :root {
    --page-bg: #f4f4f4;
    --header-bg: #ffffff;
    --ink: #222222;
    --ink-soft: #555555;
    --icon: #5a5a5a;
    --quote-bg: #454545;
    --button-bg: #1c1c1c;
    --field-bg: #ffffff;
    --field-text: #444444;
    --menu-bg: rgba(255,255,255,0.86);
    --menu-text: #333333;
  }
  * { box-sizing: border-box; margin: 0; padding: 0; }
  html, body { width: 1200px; height: 614px; overflow: hidden; background: var(--page-bg); }
  body { font-family: "Open Sans", Arial, sans-serif; color: var(--ink); }
  .canvas { position: relative; width: 1200px; height: 614px; background: var(--page-bg); }

  .site-header { position: absolute; left: 0; top: 0; width: 1200px; height: 104px; background: var(--header-bg); }
  .brand { position: absolute; left: 132px; top: 34px; height: 36px; display: flex; align-items: center; gap: 12px; }
  .brand-mark { width: 30px; height: 30px; border: 2px solid var(--ink); }
  .brand-name { font-family: "Montserrat", Arial, sans-serif; font-weight: 400; font-size: 30px; line-height: 36px; color: var(--ink); letter-spacing: 0.3px; }
  .header-tools { position: absolute; right: 134px; top: 39px; display: flex; gap: 16px; align-items: center; }
  .header-tools svg { display: block; fill: var(--icon); }

  .hero-title { position: absolute; left: 0; top: 145px; width: 1200px; text-align: center; font-family: "Montserrat", Arial, sans-serif; font-weight: 400; font-size: 41px; letter-spacing: 0; color: var(--ink); }
  .hero-subtitle { position: absolute; left: 0; top: 200px; width: 1200px; text-align: center; font-family: "Montserrat", Arial, sans-serif; font-size: 16.5px; color: var(--ink); }
  .hero-intro { position: absolute; left: 132px; top: 233px; width: 936px; text-align: center; font-size: 11.55px; line-height: 19.2px; letter-spacing: -0.05px; color: var(--ink-soft); }

  .quote-panel { position: absolute; left: 132px; top: 310px; width: 298px; height: 232px; background: var(--quote-bg); padding: 18px 16px 0; }
  .quote-title { font-family: "Montserrat", Arial, sans-serif; font-size: 16.5px; color: #ffffff; font-weight: 400; }
  .quote-field { display: flex; align-items: center; gap: 9px; width: 266px; height: 40px; background: var(--field-bg); margin-top: 16px; padding-left: 12px; font-size: 10.4px; color: var(--field-text); }
  .quote-field:first-of-type { margin-top: 18px; }
  .quote-field svg { flex: none; }
  .quote-button { display: block; width: 266px; height: 40px; margin-top: 16px; background: var(--button-bg); color: #ffffff; border: 0; font-family: "Montserrat", Arial, sans-serif; font-size: 16px; font-weight: 500; letter-spacing: 0.4px; }

  .service-showcase { position: absolute; left: 446px; top: 310px; width: 621px; height: 232px; }
  .showcase-photo { position: absolute; inset: 0; background: linear-gradient(180deg, #8eaecb 0%, #d9cdb8 28%, #9da4ac 55%, #5c5f64 78%, #8a8784 100%); }
  .service-menu { position: absolute; left: 16px; top: 32px; list-style: none; }
  .service-menu li { display: flex; align-items: center; gap: 10px; width: 256px; height: 39px; margin-bottom: 4px; background: var(--menu-bg); padding-left: 16px; font-family: "Montserrat", Arial, sans-serif; font-size: 16px; letter-spacing: 0.3px; color: var(--menu-text); }
  .service-menu svg { fill: none; stroke: var(--menu-text); stroke-width: 2; }

  .site-footer { position: absolute; left: 132px; top: 574px; width: 936px; display: flex; justify-content: space-between; align-items: center; }
  .copyright { font-size: 12px; color: #111111; word-spacing: 2px; }
  .social-links { display: flex; gap: 20px; }
  .social-links span { width: 13px; height: 13px; border-radius: 50%; background: var(--icon); display: block; }
</style>
</head>
<body>
<div class="canvas">
  <header class="site-header">
    <div class="brand">
      <span class="brand-mark"></span>
      <span class="brand-name">ROUTEWELL</span>
    </div>
    <nav class="header-tools" aria-label="Header tools">
      <svg width="18" height="16" viewBox="0 0 18 16" aria-label="Menu"><rect y="1" width="18" height="3"/><rect y="6.5" width="18" height="3"/><rect y="12" width="18" height="3"/></svg>
      <svg width="16" height="16" viewBox="0 0 24 24" aria-label="Call"><path d="M6.6 10.8a15.1 15.1 0 0 0 6.6 6.6l2.2-2.2a1 1 0 0 1 1-.25 11.4 11.4 0 0 0 3.6.57 1 1 0 0 1 1 1V20a1 1 0 0 1-1 1A17 17 0 0 1 3 4a1 1 0 0 1 1-1h3.5a1 1 0 0 1 1 1c0 1.25.2 2.45.57 3.57a1 1 0 0 1-.25 1z"/></svg>
      <svg width="16" height="16" viewBox="0 0 24 24" aria-label="Search"><circle cx="10" cy="10" r="6.5" fill="none" stroke="#5a5a5a" stroke-width="3"/><path d="M14.5 14.5 21 21" stroke="#5a5a5a" stroke-width="3.4" stroke-linecap="round"/></svg>
    </nav>
  </header>

  <h1 class="hero-title">PRIVATE &amp; BUSINESS</h1>
  <p class="hero-subtitle">Personalised Transport Service</p>
  <p class="hero-intro">Proin a dolor mauris. Vestibulum ante ipsum primis in faucibus orci luctus et ultrices posuere cubilia Curae; Vestibulum eget nisl metus. Phasellus nisl est, condimentum vitae fauci&shy;bus in, sollicitudin vel metus. Nunc sit amet consequat risus. Curabitur ac elit leo. In eleifend dui tellus, in scelerisque elit porttitor et. Integer eu massa lacinia, lacinia nulla non, volut&shy;pat purus. Sed libero felis, vestibulum et dolor eget, lacinia aliquet neque.</p>

  <section class="quote-panel">
    <h2 class="quote-title">Get Instant Quote</h2>
    <div class="quote-field">
      <svg width="12" height="12" viewBox="0 0 12 12"><circle cx="6" cy="6" r="4.6" fill="none" stroke="#555" stroke-width="2"/></svg>
      Origin (Public Location or Exact Address)
    </div>
    <div class="quote-field">
      <svg width="12" height="12" viewBox="0 0 12 14"><path d="M6 0a4.5 4.5 0 0 0-4.5 4.5C1.5 8 6 14 6 14s4.5-6 4.5-9.5A4.5 4.5 0 0 0 6 0zm0 6.3a1.8 1.8 0 1 1 0-3.6 1.8 1.8 0 0 1 0 3.6z" fill="#555"/></svg>
      Destination (Public Location or Exact Address)
    </div>
    <button class="quote-button">ESIMATE FARE</button>
  </section>

  <section class="service-showcase">
    <div class="showcase-photo" role="img" aria-label="Photo of a row of parked cars under a bright sky"></div>
    <ul class="service-menu">
      <li><svg width="8" height="12" viewBox="0 0 8 12"><path d="M2 1.5 6.5 6 2 10.5"/></svg>LIMO</li>
      <li><svg width="8" height="12" viewBox="0 0 8 12"><path d="M2 1.5 6.5 6 2 10.5"/></svg>CORPORATE CARS</li>
      <li><svg width="8" height="12" viewBox="0 0 8 12"><path d="M2 1.5 6.5 6 2 10.5"/></svg>DISABILITY TRANSIT</li>
      <li><svg width="8" height="12" viewBox="0 0 8 12"><path d="M2 1.5 6.5 6 2 10.5"/></svg>FAMILY TRANSIT SERVICE</li>
    </ul>
  </section>

  <footer class="site-footer">
    <p class="copyright">Copyright © 2017 RouteWell. All rights reserved.</p>
    <div class="social-links" aria-label="Social links">
      <span></span><span></span><span></span>
    </div>
  </footer>
</div>
</body>
</html>
```